Local Flower Farm Needs Business Card Design

I need business cards designed for a flower farm based in Eudora, Kansas.
Business Info:
We are a local cut flower farm located in Eudora, Kansas, founded by Corinne Haldwick. What started as a passion for agriculture and search for more joy in daily life has blossomed into a small business dedicated to providing the community with beautiful, fresh, and sustainable flowers. We specialize in local, seasonal blooms, ensuring that every petal reflects the care and dedication we pour into our craft. Our mission is to deliver the highest quality flowers directly to our customers through local farmers markets and to florists who share our commitment to sustainability. Join us in celebrating the beauty of nature, one bloom at a time!
Contact Details:
Corinne Haldwick
Owner
Phone 913-555-0147
Facebook: Rosalind Thorpe Gardens
Instagram: @RosalindThorpeGardens
Website: RosalindThorpeGardens.example
Target Market(s)
Wholesale to Florists and Direct to Consumer via Farmers Market
Industry/Entity Type
Florist, Farm
Contact Information for Business Card
Name, Contact Info, Logo
Look and feel
Each slider illustrates characteristics of the customer's brand and the style your logo design should communicate.

```html
<!DOCTYPE html>
<html lang="en">
<head>
<meta charset="utf-8">
<title>Rosalind Thorpe Gardens – Business Card</title>
<link rel="stylesheet" href="https://fonts.googleapis.com/css2?family=Montserrat:wght@400;500;700&display=swap">
<style>
  :root {
    --backdrop: #9a9a9a;
    --card-white: #ffffff;
    --ink: #0b2a30;
    --text: #141c1e;
    --deep-teal: #0a262c;
    --bright-teal: #52c4e0;
    --rule: #7d8587;
  }
  * { box-sizing: border-box; margin: 0; padding: 0; }
  html, body {
    width: 1093px; height: 1200px; overflow: hidden;
    background: var(--backdrop);
    font-family: "Montserrat", sans-serif;
  }
  .card {
    position: absolute; left: 264px; width: 597px;
    border-radius: 18px; overflow: hidden;
    box-shadow: 0 0 0 1.5px #2b2b2b;
  }
  .card-front { top: 225px; height: 363px; background: var(--card-white); }
  .card-back { top: 615px; height: 367px; background: var(--deep-teal); }

  .holder-name {
    position: absolute; left: 30px; top: 38px;
    font-size: 23px; font-weight: 700; color: var(--ink); letter-spacing: 0.1px;
  }
  .holder-role {
    position: absolute; left: 30px; top: 70px;
    font-size: 14px; font-weight: 400; color: var(--text);
  }
  .brand-seal {
    position: absolute; left: 426px; top: 33px; width: 128px; height: 128px;
    border: 1px solid var(--rule); border-radius: 50%;
    display: flex; align-items: center; justify-content: center; text-align: center;
    font-size: 13px; font-weight: 700; color: var(--ink); line-height: 1.3;
    padding: 0 14px;
  }
  .contact-list {
    position: absolute; left: 30px; top: 252px; list-style: none;
  }
  .contact-list li {
    display: flex; align-items: center; gap: 7px;
    height: 21.5px; font-size: 13.5px; color: var(--text);
  }
  .contact-list svg { width: 13px; height: 13px; flex: none; }
  .address {
    position: absolute; left: 405px; top: 302px;
    font-size: 13.5px; color: var(--text); line-height: 16.5px; font-style: normal;
  }

  .monogram-field {
    position: absolute; inset: 0;
    background: linear-gradient(135deg, var(--bright-teal) 0%, #2f7f92 22%, #123c44 48%, var(--deep-teal) 70%);
    opacity: 0.9;
  }
  .back-mark {
    position: absolute; left: 392px; top: 232px; width: 80px;
    font-size: 11px; font-weight: 700; color: var(--card-white);
    line-height: 1.3; text-align: center;
  }
</style>
</head>
<body>
  <section class="card card-front">
    <h1 class="holder-name">Corinne Haldwick</h1>
    <p class="holder-role">Owner</p>
    <div class="brand-seal">Rosalind Thorpe Gardens</div>

    <ul class="contact-list">
      <li>
        <svg viewBox="0 0 24 24" aria-hidden="true"><path fill="var(--ink)" d="M6.6 10.8a15.1 15.1 0 0 0 6.6 6.6l2.2-2.2a1 1 0 0 1 1-.25 11.4 11.4 0 0 0 3.6.57 1 1 0 0 1 1 1V20a1 1 0 0 1-1 1A17 17 0 0 1 3 4a1 1 0 0 1 1-1h3.5a1 1 0 0 1 1 1c0 1.25.2 2.45.57 3.57a1 1 0 0 1-.25 1z"/></svg>
        913-555-0147
      </li>
      <li>
        <svg viewBox="0 0 24 24" aria-hidden="true"><circle cx="12" cy="12" r="11" fill="var(--ink)"/></svg>
        Rosalind Thorpe Gardens
      </li>
      <li>
        <svg viewBox="0 0 24 24" aria-hidden="true"><circle cx="12" cy="12" r="11" fill="var(--ink)"/></svg>
        @RosalindThorpeGardens
      </li>
      <li>
        <svg viewBox="0 0 24 24" aria-hidden="true"><circle cx="12" cy="12" r="10" fill="none" stroke="var(--ink)" stroke-width="2.4"/><path d="M2 12h20M12 2c3 3 3 17 0 20M12 2c-3 3-3 17 0 20" fill="none" stroke="var(--ink)" stroke-width="1.8"/></svg>
        www.RosalindThorpeGardens.example
      </li>
    </ul>

    <address class="address">418 Meadowlark Ln, #12<br>Eudora, KS 66025</address>
  </section>

  <section class="card card-back">
    <div class="monogram-field" role="img" aria-label="Repeating brand monogram pattern fading from bright teal to deep teal"></div>
    <div class="back-mark">Rosalind Thorpe Gardens</div>
  </section>
</body>
</html>
```